Business cards to launch an education platform

Hi,
I am looking at having new business cards designed.
I am a startup, developing a web platform for schools and university, the education world. It's an online assessment system.
I would like a card that looks classy, and that is using the colors and the font of my logo.

I have attached:
1) my logo
2) A business card that I have designed quickly so you can have all the information required in the card, but I really don't like it.
3) The font that I am using (Lato Regular) to design my web platform
4) Some screenshots of my web platform so you can have a look at the style that I have.

Target Market(s)

Major market: Education system: Schools and university
Minor markets: Business in general

Industry/Entity Type

Business

Contact Information for Business Card

Clara Fenwick
Director

M: 0437 518 902
E: clara.fenwick@amberLoomSystems.com.au

Requirements
Must have
• The colors of my logo

```html
<!DOCTYPE html>
<html lang="en">
<head>
<meta charset="utf-8">
<title>Amber Loom Systems – Business Cards</title>
<link rel="stylesheet" href="https://fonts.googleapis.com/css2?family=Lato:wght@400;700&display=swap">
<style>
  :root {
    --backdrop: #e4e2de;
    --card: #fbfbfb;
    --navy: #123f6e;
    --sky: #25a6e0;
    --ink: #3a3a3a;
    --emboss: #ececec;
  }
  * { margin: 0; padding: 0; box-sizing: border-box; }
  html, body { width: 1200px; height: 950px; overflow: hidden; }
  body {
    position: relative;
    background: var(--backdrop);
    font-family: "Lato", Arial, sans-serif;
  }
  .card {
    position: absolute;
    width: 670px;
    height: 384px;
    background: var(--card);
    box-shadow: 4px 6px 14px rgba(0,0,0,0.28);
  }
  .card--front { left: 155px; top: 117px; z-index: 2; }
  .card--back { left: 393px; top: 461px; z-index: 1; }

  .brand { position: absolute; display: flex; align-items: center; gap: 22px; }
  .brand__mark { width: 96px; height: 96px; background: var(--navy); }
  .brand__name {
    color: var(--navy);
    font-weight: 400;
    line-height: 1.05;
  }
  .brand__line1 { display: block; font-size: 32px; letter-spacing: 2px; }
  .brand__line2 { display: block; font-size: 26px; letter-spacing: 1px; }
  .card--front .brand { left: 42px; top: 38px; }

  .contact { position: absolute; left: 42px; top: 232px; color: var(--ink); }
  .contact__name { font-size: 23px; font-weight: 700; color: var(--navy); letter-spacing: 0.5px; }
  .contact__role { font-size: 16px; color: var(--sky); letter-spacing: 0.5px; margin-top: 2px; }
  .contact__list { list-style: none; margin-top: 16px; font-size: 16px; }
  .contact__item { display: flex; align-items: center; gap: 10px; height: 24px; }
  .contact__item svg { width: 14px; height: 14px; flex: none; }

  .accent-square {
    position: absolute; left: 484px; top: 206px;
    width: 130px; height: 130px; background: var(--navy);
  }

  .faint-square {
    position: absolute; left: 48px; top: 206px;
    width: 128px; height: 128px;
    background: var(--emboss);
    box-shadow: inset 1px 1px 2px rgba(0,0,0,0.12), inset -1px -1px 2px rgba(255,255,255,0.9);
  }
  .card--back .brand__name { position: absolute; right: 38px; top: 258px; text-align: left; }
  .card--back .brand__line1 { font-size: 38px; letter-spacing: 3px; }
  .card--back .brand__line2 { font-size: 30px; letter-spacing: 2px; }
</style>
</head>
<body>
  <section class="card card--front" aria-label="Business card front">
    <div class="brand">
      <div class="brand__mark" aria-hidden="true"></div>
      <div class="brand__name">
        <span class="brand__line1">AMBER</span>
        <span class="brand__line2">Loom systems</span>
      </div>
    </div>

    <div class="contact">
      <p class="contact__name">CLARA FENWICK</p>
      <p class="contact__role">DIRECTOR</p>
      <ul class="contact__list">
        <li class="contact__item">
          <svg viewBox="0 0 14 14" aria-hidden="true"><rect x="3" y="0.5" width="8" height="13" rx="1.5" fill="none" stroke="#123f6e" stroke-width="1.4"/><rect x="4.6" y="2.2" width="4.8" height="8" fill="#123f6e"/></svg>
          <span>0437 518 902</span>
        </li>
        <li class="contact__item">
          <svg viewBox="0 0 14 14" aria-hidden="true"><rect x="0.5" y="2.5" width="13" height="9" fill="#123f6e"/><path d="M0.8 3 L7 8 L13.2 3" fill="none" stroke="#fbfbfb" stroke-width="1.1"/></svg>
          <span>clara.fenwick@amberLoomSystems.com.au</span>
        </li>
      </ul>
    </div>

    <div class="accent-square" aria-hidden="true"></div>
  </section>

  <section class="card card--back" aria-label="Business card back">
    <div class="faint-square" aria-hidden="true"></div>
    <div class="brand__name">
      <span class="brand__line1">AMBER</span>
      <span class="brand__line2">Loom systems</span>
    </div>
  </section>
</body>
</html>
```